Franchise Power Point

Looking to add a strong design element to a very basic power point presentation about how to find the ideal franchise match. My website is www.tallowbrookventuring.com and www.unitquest/KWendell

```html
<!DOCTYPE html>
<html lang="en">
<head>
<meta charset="utf-8">
<title>Smart Franchise Decisions Using Logic and Intuition</title>
<link href="https://fonts.googleapis.com/css2?family=Libre+Baskerville:wght@400;700&family=Poppins:wght@400;500&display=swap" rel="stylesheet">
<style>
:root{
  --cream:#fcf6e4;
  --navy:#1b3247;
  --gold:#f2b825;
  --gold-soft:#f8d45c;
  --ink:#2a3340;
  --white:#ffffff;
}
*{box-sizing:border-box;margin:0;padding:0}
html,body{width:1200px;height:4051px;overflow:hidden;background:var(--cream)}
body{position:relative;font-family:"Poppins",sans-serif;color:var(--ink)}
.slide{position:absolute;left:75px;width:1048px;height:590px;background:var(--white);overflow:hidden;box-shadow:0 4px 14px rgba(0,0,0,.12)}
.slide-title{position:absolute;left:61px;top:34px;font-family:"Libre Baskerville",serif;font-size:25px;line-height:35px;color:var(--navy);text-transform:uppercase;letter-spacing:.3px}
.title-rule{position:absolute;left:0;top:120px;width:150px;height:3px;background:var(--gold)}
.title-rule::after{content:"";position:absolute;right:-6px;top:-6px;width:15px;height:15px;border-radius:50%;background:var(--gold)}
.brand{position:absolute;left:775px;top:56px;font-family:"Poppins",sans-serif;font-weight:500;font-size:28px;line-height:36px;color:var(--navy)}
.footer-rule{position:absolute;left:0;right:0;top:561px;height:2px;background:var(--gold-soft)}
.page-num{position:absolute;left:952px;top:544px;width:34px;height:34px;border-radius:50%;background:var(--navy);color:var(--white);font-size:13px;font-weight:500;display:flex;align-items:center;justify-content:center}
.bullets{position:absolute;list-style:none;font-size:13.5px;line-height:19px}
.bullets li{position:relative;padding-left:29px;margin-bottom:13px}
.bullets li::before{content:"";position:absolute;left:0;top:4px;width:7px;height:7px;border:3px solid var(--gold);border-radius:50%}
.photo{position:absolute;border-radius:50%}

/* slide 1 */
.cover{top:86px}
.cover .photo-bg{position:absolute;left:0;top:0;width:1048px;height:590px;background:linear-gradient(120deg,#7fb7b5 0%,#2e5a61 45%,#1a2b33 100%)}
.cover svg{position:absolute;left:0;top:0}
.cover .brand{left:61px;top:60px;color:var(--white)}
.cover-title{position:absolute;left:61px;top:212px;font-family:"Libre Baskerville",serif;font-size:31px;line-height:44px;color:var(--white);text-transform:uppercase}
.cover .title-rule{top:346px;width:150px}
.cover-sub{position:absolute;left:61px;top:382px;font-size:28px;line-height:40px;color:var(--white);font-weight:500}

/* slide 2 */
.approach{top:744px}
.approach .bullets{left:61px;top:250px;width:520px}
.approach .ring{left:604px;top:125px;width:386px;height:386px;border-radius:50%;background:var(--gold)}
.approach .photo{left:596px;top:133px;width:380px;height:380px;background:linear-gradient(150deg,#b9c4c8,#6e7b80 60%,#3d4549)}

/* slide 3 */
.questions{top:1402px}
.questions .ring{left:61px;top:153px;width:386px;height:386px;border-radius:50%;background:var(--navy)}
.questions .photo{left:75px;top:163px;width:376px;height:376px;background:linear-gradient(140deg,#d8c6a8,#8a6d4e 60%,#4a3a2b)}
.questions .bullets{left:502px;top:177px;font-size:13.5px}
.questions .bullets li{margin-bottom:11.5px}

/* slide 4 */
.research{top:2060px}
.research .photo{left:102px;top:126px;width:845px;height:245px;border-radius:123px;background:linear-gradient(90deg,#7a5a42,#a48466 45%,#8b6a4f)}
.research .col-a{left:200px;top:400px}
.research .col-b{left:546px;top:400px}
.research .bullets li{margin-bottom:11.5px}

/* slide 5 */
.booth{top:2717px}
.booth .panel{position:absolute;left:101px;top:0;width:410px;height:590px;background:linear-gradient(160deg,#1f3448,#0f1b26)}
.booth .frame{position:absolute;left:116px;top:84px;width:326px;height:466px;border:4px solid var(--white)}
.booth .book{position:absolute;left:61px;top:53px;width:356px;height:447px;background:linear-gradient(180deg,#2e5873 0 33%,#ffffff 33% 88%,#2e5873 88%)}
.booth-title{position:absolute;left:577px;top:170px;font-family:"Libre Baskerville",serif;font-size:29px;line-height:41px;color:var(--navy);text-transform:uppercase}
.booth .booth-rule{position:absolute;left:511px;top:400px;width:152px;height:3px;background:var(--gold)}
.booth .booth-rule::after{content:"";position:absolute;right:-6px;top:-6px;width:15px;height:15px;border-radius:50%;background:var(--gold)}

/* slide 6 */
.contact{top:3375px}
.contact .ring{left:61px;top:100px;width:384px;height:384px;border-radius:50%;background:linear-gradient(180deg,var(--gold-soft),var(--gold))}
.contact .photo{left:79px;top:118px;width:348px;height:348px;background:linear-gradient(160deg,#e9e4dc,#c9a47a 50%,#9a2a30)}
.contact-list{position:absolute;left:499px;top:238px;list-style:none}
.contact-list li{display:flex;align-items:center;height:54px;font-size:21px;color:var(--navy)}
.contact-list svg{width:20px;height:20px;margin-right:11px;flex:none}
</style>
</head>
<body>

<section class="slide cover">
  <div class="photo-bg" role="img" aria-label="Hands typing on a laptop with glowing storefront and business icons"></div>
  <svg width="1048" height="590" viewBox="0 0 1048 590">
    <path d="M0 0 H546 Q690 295 572 590 H0 Z" fill="#1b3247"/>
    <path d="M552 0 Q700 295 578 590" fill="none" stroke="#f2b825" stroke-width="9"/>
  </svg>
  <div class="brand">UnitQuest</div>
  <h1 class="cover-title">Smart Franchise<br>Decisions Using Logic<br>and Intuition</h1>
  <div class="title-rule"></div>
  <p class="cover-sub">Helping People Realize<br>Their Dreams</p>
</section>

<section class="slide approach">
  <h2 class="slide-title">What is the Educated<br>Approach?</h2>
  <div class="title-rule"></div>
  <div class="brand">UnitQuest</div>
  <ul class="bullets">
    <li>First Define the Ideal Fit</li>
    <li>Focus on options that fit your strengths</li>
    <li>Focus on options that will meet your lifestyle and financial goals while reducing risk</li>
    <li>Put yourself at the center of the search</li>
  </ul>
  <div class="photo ring"></div>
  <div class="photo" role="img" aria-label="Shop owner standing with arms crossed in her store"></div>
  <div class="footer-rule"></div><div class="page-num">2</div>
</section>

<section class="slide questions">
  <h2 class="slide-title">Sample Key Questions for the<br>Educated Approach</h2>
  <div class="title-rule"></div>
  <div class="brand">UnitQuest</div>
  <div class="photo ring"></div>
  <div class="photo" role="img" aria-label="Business owner in an apron reviewing paperwork at a laptop"></div>
  <ul class="bullets">
    <li>Proper investment level</li>
    <li>Skill set and background / personality matching</li>
    <li>Return goals – short, mid and long term</li>
    <li>Employee profile: numbers &amp; backgrounds</li>
    <li>Sales, marketing and advertising</li>
    <li>Concerns around the economy</li>
    <li>Need vs want</li>
    <li>Residual / Repeat / Reoccurring</li>
    <li>Status</li>
    <li>B2B vs B2C</li>
    <li>Full time vs part time vs. managed services</li>
  </ul>
  <div class="footer-rule"></div><div class="page-num">3</div>
</section>

<section class="slide research">
  <h2 class="slide-title">The Research Method</h2>
  <div class="title-rule" style="top:86px"></div>
  <div class="brand">UnitQuest</div>
  <div class="photo" role="img" aria-label="Two women working at a wooden table seen from above"></div>
  <ul class="bullets col-a">
    <li>Define your ideal match</li>
    <li>Establish contact with target franchisor</li>
    <li>Work through their standard process</li>
    <li>Review FDD</li>
    <li>Validate with franchisees</li>
  </ul>
  <ul class="bullets col-b">
    <li>Explore financing options</li>
    <li>Discuss territory</li>
    <li>Put together cash flow projections</li>
    <li>Attend Discovery Day</li>
    <li>Make a decision</li>
  </ul>
  <div class="footer-rule"></div><div class="page-num">4</div>
</section>

<section class="slide booth">
  <div class="panel" role="img" aria-label="Dark photo of a person reading"></div>
  <div class="frame"></div>
  <div class="book" role="img" aria-label="Cover of the book The Owner's Field Guide, second edition, by Dale Morrow and Kara Wendell"></div>
  <div class="brand">UnitQuest</div>
  <h2 class="booth-title">Stop by my booth,<br>ask me any question<br>and receive a free<br>copy of the Owner's<br>Field Guide</h2>
  <div class="booth-rule"></div>
  <div class="footer-rule"></div><div class="page-num">5</div>
</section>

<section class="slide contact">
  <h2 class="slide-title">Courtesy of:</h2>
  <div class="title-rule" style="top:86px"></div>
  <div class="brand">UnitQuest</div>
  <div class="photo ring"></div>
  <div class="photo" role="img" aria-label="Portrait of franchise consultant Kara Wendell"></div>
  <ul class="contact-list">
    <li><svg viewBox="0 0 20 20"><circle cx="10" cy="10" r="9" fill="none" stroke="#f2b825" stroke-width="2"/><circle cx="10" cy="8" r="3" fill="#f2b825"/><path d="M4.5 16 Q10 10 15.5 16" fill="#f2b825"/></svg>Kara Wendell</li>
    <li><svg viewBox="0 0 20 20"><path d="M4 2 L7.5 2 L9 6 L7 7.5 Q8.5 11 12.5 13 L14 11 L18 12.5 L18 16 Q17 18 14.5 18 Q3 16 2 5 Q2 2.5 4 2Z" fill="#f2b825"/></svg>555.014.2207</li>
    <li><svg viewBox="0 0 20 20"><rect x="2" y="4" width="16" height="12" rx="1.5" fill="#f2b825"/><path d="M2.5 5 L10 11 L17.5 5" fill="none" stroke="#fff" stroke-width="1.5"/></svg>kwendell@unitquest.com</li>
    <li><svg viewBox="0 0 20 20"><circle cx="10" cy="10" r="8.5" fill="#f2b825"/><path d="M1.5 10 H18.5 M10 1.5 Q5 10 10 18.5 M10 1.5 Q15 10 10 18.5" fill="none" stroke="#fff" stroke-width="1.2"/></svg>http://www.tallowbrookventuring.com</li>
  </ul>
  <div class="footer-rule"></div><div class="page-num">6</div>
</section>

</body>
</html>
```